Elevating our current Business Card Design

We want to elevate our current business card with a new design to look like a zenith 300 company. We are a premium lubricant distributor (oil and grease).
We need 2 versions, version 1 is as per the uploaded a copy of our current business card with the English version.
For our Chinese version we need to use the front to be English in English and have the back of the card designed exactly like the front for all info to be in Chinese.
The design template needs to be such that we can amend the template with adding different information for each person's card.
The background colour of the card can be changed- we just need to clearly see all information on the card and logos.
The QJR and Ember steady logos cannot have any colour or display changes- only use the logos attached.
All logos need to be included and all information from the attached current card

```html
<!DOCTYPE html>
<html lang="en">
<head>
<meta charset="utf-8">
<title>Meridian Business Card</title>
<link rel="stylesheet" href="https://fonts.googleapis.com/css2?family=Open+Sans:wght@400;600;700&display=swap">
<style>
  :root {
    --stage: #232323;
    --card: #212126;
    --card-back: #1b1b1f;
    --mark-dark: #0c0c0e;
    --red: #e8262a;
    --white: #ffffff;
    --badge: #4a4a50;
  }
  * { box-sizing: border-box; margin: 0; padding: 0; }
  html, body {
    width: 1200px; height: 780px; overflow: hidden;
    background: var(--stage);
    font-family: "Open Sans", Arial, sans-serif;
  }
  .stage { position: relative; width: 1200px; height: 780px; }
  .card {
    position: absolute; top: 230px;
    width: 560px; height: 320px;
    border-bottom: 4px solid var(--red);
    overflow: hidden;
  }
  .card--back { left: 30px; background: var(--card-back); }
  .card--front { left: 610px; background: var(--card); }

  /* back side */
  .back-mark {
    position: absolute; inset: 0;
    display: flex; align-items: center; justify-content: center; gap: 18px;
  }
  .back-mark__dot { width: 46px; height: 46px; border-radius: 50%; background: var(--mark-dark); }
  .back-mark__name { font-size: 96px; font-weight: 700; color: var(--mark-dark); letter-spacing: -2px; }

  /* front side */
  .brand {
    position: absolute; left: 30px; top: 70px;
    display: flex; align-items: center; gap: 12px;
  }
  .brand__dot { width: 26px; height: 26px; border-radius: 50%; background: var(--red); }
  .brand__name { font-size: 46px; font-weight: 700; color: var(--red); letter-spacing: -1px; }

  .person { position: absolute; right: 34px; top: 28px; text-align: right; }
  .person__name { font-size: 28px; font-weight: 600; color: var(--red); line-height: 1.1; }
  .person__title { font-size: 13.5px; color: var(--white); margin-top: 2px; }
  .person-tab { position: absolute; right: 0; top: 28px; width: 20px; height: 44px; background: var(--red); }

  .address {
    position: absolute; left: 52px; top: 168px;
    font-size: 13.5px; line-height: 18px; color: var(--white); font-style: normal;
  }
  .contacts {
    position: absolute; left: 30px; top: 212px; list-style: none;
    font-size: 12.5px; line-height: 18px; color: var(--white);
  }
  .contacts li { display: flex; align-items: center; gap: 8px; }
  .contacts svg { width: 13px; height: 13px; flex: none; }

  .ember {
    position: absolute; left: 318px; top: 196px; width: 70px; text-align: center;
    color: var(--white); font-size: 13px; font-weight: 700; line-height: 14px;
  }
  .certs { position: absolute; left: 404px; top: 172px; display: flex; gap: 14px; }
  .cert { width: 34px; height: 34px; border-radius: 50%; background: var(--badge); }

  .partners {
    position: absolute; left: 318px; top: 236px; width: 226px; height: 62px;
    display: flex; border: 2px solid var(--red); border-radius: 5px; overflow: hidden;
  }
  .partners__client { flex: 1; display: flex; align-items: center; gap: 6px; padding-left: 8px; }
  .partners__dot { width: 8px; height: 8px; border-radius: 50%; background: var(--red); }
  .partners__name { font-size: 10px; line-height: 12px; font-weight: 600; color: var(--red); }
  .partners__supplier {
    width: 112px; background: var(--red); color: var(--white);
    display: flex; flex-direction: column; justify-content: center; padding-left: 10px;
  }
  .partners__brand { font-size: 19px; font-weight: 700; line-height: 20px; }
  .partners__tag { font-size: 8px; font-weight: 600; letter-spacing: .3px; }
</style>
</head>
<body>
<main class="stage">

  <section class="card card--back" aria-label="Card back">
    <div class="back-mark">
      <span class="back-mark__dot"></span>
      <span class="back-mark__name">Meridian</span>
    </div>
  </section>

  <section class="card card--front" aria-label="Card front">
    <div class="brand">
      <span class="brand__dot"></span>
      <span class="brand__name">Meridian</span>
    </div>

    <div class="person">
      <p class="person__name">Nora Vance</p>
      <p class="person__title">Administration Executive</p>
    </div>
    <span class="person-tab"></span>

    <address class="address">48 Depot Road<br>Harlow Park, WA 6190</address>

    <ul class="contacts">
      <li>
        <svg viewBox="0 0 16 16"><path fill="#e8262a" d="M3 1l3 3-2 2c1 2 3 4 5 5l2-2 3 3-2 3C7 15 1 9 1 3z"/></svg>
        1300 000 412
      </li>
      <li>
        <svg viewBox="0 0 16 16"><rect x="4" y="1" width="8" height="14" rx="1.5" fill="none" stroke="#e8262a" stroke-width="1.5"/></svg>
        +61 400 118 274
      </li>
      <li>
        <svg viewBox="0 0 16 16"><rect x="1" y="6" width="14" height="9" rx="1" fill="#e8262a"/><rect x="4" y="1" width="8" height="5" fill="none" stroke="#e8262a" stroke-width="1.5"/></svg>
        +61 8 9000 3316
      </li>
      <li>
        <svg viewBox="0 0 16 16"><circle cx="8" cy="8" r="6.5" fill="none" stroke="#e8262a" stroke-width="1.5"/><path d="M1.5 8h13M8 1.5c-3 3.5-3 9.5 0 13M8 1.5c3 3.5 3 9.5 0 13" fill="none" stroke="#e8262a" stroke-width="1.2"/></svg>
        www.meridianlube.com
      </li>
      <li>
        <svg viewBox="0 0 16 16"><rect x="1" y="3" width="14" height="10" rx="1" fill="#e8262a"/><path d="M1.5 4L8 9l6.5-5" fill="none" stroke="#212126" stroke-width="1.3"/></svg>
        nora.vance@meridianlube.com
      </li>
    </ul>

    <p class="ember">Ember steady</p>

    <div class="certs">
      <span class="cert" role="img" aria-label="Certification badge"></span>
      <span class="cert" role="img" aria-label="Certification badge"></span>
      <span class="cert" role="img" aria-label="Certification badge"></span>
    </div>

    <div class="partners">
      <div class="partners__client">
        <span class="partners__dot"></span>
        <span class="partners__name">Meridian<br>Lube Supply</span>
      </div>
      <div class="partners__supplier">
        <span class="partners__brand">ORVANE</span>
        <span class="partners__tag">PREMIUM LUBRICANTS</span>
      </div>
    </div>
  </section>

</main>
</body>
</html>
```